Blue Harbor Mortgages Social Media Campaign

I need social media campaign banners. Facebook and Instagram.
I would like them to incorporate local photos, my photo and my logo. I have some sample files of previous campaigns and I have a color scheme associated with my brand. My business operates in St. John's Newfoundland.

Target Market(s)

Home Buyers, Home Owners

Industry/Entity Type

Mortgage Brokering

Logo Text

Blue Harbor Mortgages

Logo styles of interest
Lettermark Logo
Font styles to use
Other font styles liked:
• Times New Roman, I'm open to suggestion

Colors
0054AA
0677BA
7BADD7
CADEEF
E8F1F8
EE7325
F08F49
F5BC92
FAE3D3
FDF4ED

Requirements
Must have
• My name, photo, contact info, slogan
Nice to have
• We can discuss slogans to use, I can provide some suggestions.

```html
<!DOCTYPE html>
<html lang="en">
<head>
<meta charset="UTF-8">
<title>Blue Harbor Mortgages – Social Banner</title>
<link href="https://fonts.googleapis.com/css2?family=Montserrat:wght@400;500;700;800&display=swap" rel="stylesheet">
<style>
  :root{
    --navy:#0d1c5e;
    --orange:#fd4c0c;
    --white:#ffffff;
    --button-blue:#0b4fb0;
    --stage:#ffffff;
    --hex-border:#c8d2ea;
  }
  *{margin:0;padding:0;box-sizing:border-box;}
  html,body{width:1200px;height:814px;overflow:hidden;background:var(--stage);}
  body{font-family:"Montserrat",sans-serif;position:relative;}
  .banner{position:absolute;left:0;top:93px;width:1200px;height:627px;background:var(--navy);overflow:hidden;}
  .shapes{position:absolute;inset:0;}
  .brand{position:absolute;left:60px;top:120px;width:310px;text-align:center;color:var(--white);}
  .brand-name{font-size:25px;font-weight:800;letter-spacing:.2px;line-height:1;}
  .brand-tagline{display:flex;align-items:center;justify-content:center;gap:8px;margin-top:6px;font-size:11px;font-weight:700;letter-spacing:1.6px;}
  .brand-tagline::before,.brand-tagline::after{content:"";width:32px;height:2px;background:var(--white);}
  .headline{position:absolute;left:58px;top:266px;font-weight:800;line-height:1;}
  .headline-top{font-size:42px;color:var(--white);display:block;}
  .headline-accent{font-size:45px;color:var(--orange);display:block;margin-top:7px;}
  .rule{position:absolute;left:60px;top:366px;width:420px;height:3px;background:var(--white);}
  .pitch{position:absolute;left:58px;top:380px;font-size:26px;line-height:39px;color:var(--white);font-weight:400;}
  .pitch strong{font-weight:700;}
  .call-label{position:absolute;left:55px;top:460px;font-size:27px;font-weight:800;color:var(--orange);}
  .phone{position:absolute;left:55px;top:498px;display:flex;align-items:center;gap:14px;color:var(--white);font-size:44px;font-weight:800;}
  .phone svg{width:30px;height:30px;}
  .cta{position:absolute;left:573px;top:493px;width:205px;height:46px;background:var(--button-blue);border-radius:3px;color:var(--white);font-size:26px;font-weight:500;display:flex;align-items:center;justify-content:center;gap:4px;}
  .cta-arrows{color:var(--orange);font-weight:800;letter-spacing:-4px;}
  .contact-band{position:absolute;left:0;top:562px;width:860px;height:65px;background:var(--orange);display:flex;align-items:center;padding-left:55px;gap:12px;color:var(--white);font-size:22px;}
  .contact-band strong{font-weight:700;}
  .contact-item{display:flex;align-items:center;gap:5px;}
  .contact-item svg{width:22px;height:22px;}
  .divider{font-weight:700;}
</style>
</head>
<body>
  <section class="banner">
    <svg class="shapes" width="1200" height="627" viewBox="0 0 1200 627">
      <defs>
        <linearGradient id="scenery" x1="0" y1="0" x2="0" y2="1">
          <stop offset="0" stop-color="#2e7fd6"/>
          <stop offset=".35" stop-color="#5f8f3a"/>
          <stop offset="1" stop-color="#7a8a6a"/>
        </linearGradient>
        <linearGradient id="house" x1="0" y1="0" x2="1" y2="1">
          <stop offset="0" stop-color="#f2f2f2"/>
          <stop offset="1" stop-color="#d9c7b4"/>
        </linearGradient>
        <linearGradient id="portrait" x1="0" y1="0" x2="0" y2="1">
          <stop offset="0" stop-color="#d8b48a"/>
          <stop offset=".5" stop-color="#c89a74"/>
          <stop offset=".62" stop-color="#1a2455"/>
          <stop offset="1" stop-color="#141c48"/>
        </linearGradient>
      </defs>
      <path d="M0,0 H417 C440,40 430,110 380,160 C330,200 280,245 240,247 C200,248 120,180 0,140 Z" fill="var(--orange)"/>
      <path role="img" aria-label="Photo of colourful hillside houses under green cliffs in St. John's" d="M417,0 H1200 V245 C1150,270 1110,340 1030,365 C960,385 900,370 840,340 L700,240 C640,170 560,160 500,120 C450,85 430,40 417,0 Z" fill="url(#scenery)"/>
      <polygon role="img" aria-label="Photo of hands holding a small model house and keys" points="680,150 792,212 792,346 680,408 568,346 568,212" fill="url(#house)" stroke="var(--hex-border)" stroke-width="6"/>
      <path role="img" aria-label="Portrait photo of the mortgage broker" d="M855,627 C860,500 900,420 960,380 C930,300 940,130 1030,112 C1120,100 1140,300 1120,380 C1170,400 1200,430 1200,460 V627 Z" fill="url(#portrait)"/>
    </svg>

    <div class="brand">
      <div class="brand-name">BLUE HARBOR MORTGAGES</div>
      <div class="brand-tagline">WE THINK OUTSIDE THE BOX</div>
    </div>

    <h1 class="headline">
      <span class="headline-top">WE THINK</span>
      <span class="headline-accent">OUTSIDE THE BOX</span>
    </h1>
    <div class="rule"></div>

    <p class="pitch">We Get <strong>The Lowest Rates</strong> and<br>Best Deals <strong>For Our Clients</strong></p>

    <div class="call-label">Call Maren:</div>
    <div class="phone">
      <svg viewBox="0 0 24 24" aria-hidden="true"><path fill="#fff" d="M6.6 10.8a15.1 15.1 0 0 0 6.6 6.6l2.2-2.2a1 1 0 0 1 1-.25 11.4 11.4 0 0 0 3.6.57 1 1 0 0 1 1 1V20a1 1 0 0 1-1 1A17 17 0 0 1 3 4a1 1 0 0 1 1-1h3.5a1 1 0 0 1 1 1c0 1.25.2 2.45.57 3.57a1 1 0 0 1-.25 1z"/><path fill="none" stroke="#fff" stroke-width="1.6" d="M14 2.5a7.5 7.5 0 0 1 7.5 7.5M14 6a4 4 0 0 1 4 4"/></svg>
      <span>709-555-0148</span>
    </div>

    <div class="cta">Get Started <span class="cta-arrows">❯❯</span></div>

    <footer class="contact-band">
      <span class="contact-item">
        <svg viewBox="0 0 24 24" aria-hidden="true"><circle cx="12" cy="12" r="10" fill="none" stroke="#fff" stroke-width="1.5"/><path d="M2 12h20M12 2c3 3 3 17 0 20M12 2c-3 3-3 17 0 20" fill="none" stroke="#fff" stroke-width="1.2"/></svg>
        <span>www.<strong>blueharbormtg</strong>.com</span>
      </span>
      <span class="divider">|</span>
      <span class="contact-item">
        <svg viewBox="0 0 24 24" aria-hidden="true"><circle cx="12" cy="12" r="10" fill="none" stroke="#fff" stroke-width="1.5"/><rect x="7" y="8.5" width="10" height="7" fill="#fff"/><path d="M7 8.5l5 4 5-4" fill="none" stroke="var(--orange)" stroke-width="1.2"/></svg>
        <span>info@<strong>blueharbormtg</strong>.com</span>
      </span>
    </footer>
  </section>
</body>
</html>
```